Flyer-Design für Ofenservice Firma
Zielgruppe
Die Firma hat als Kerngeschäft Wartung, Reinigung, Reparatur und Inbetriebnahme von Öfen und Kaminen aller Art. Der Fokus liegt dabei auf Pelletöfen. Die Firma versteht sich als zuverlässiger Dienstleister mit gutem Preisleistungsverhältnis. Zielgruppe sind hauptsächlich private Bewohner von Einfamilienhäusern in der ländlichen Gegend (Hessen)
Aufgabenstellung
Zur Bekanntmachung nach Neugründung soll ein Faltflyer gestaltet werden mit insgesamt 6 Bereichen. Die Informationen, welche auf den Flyer sollen, entnehmen Sie bitte dem Entwurf (flyer.pdf). Dieser stellt nur eine erste Idee dar und darf gerne nach Belieben verändert bzw. neu gestaltet werden. Die enthaltenen Informationen, sollten im Großen und Ganzen aber beibehalten werden. Schön wäre evtl. auch eine Hervorhebung der Preise, da wir Preisführer im Markt sind. Auch die Bilder unseres Teams sollen in den Flyer integriert sein. Auf Anfrage kann ich auch gerne weitere Kamin- und Ofenfotos zur Verfügung stellen, für welche ich die Nutzungsrechte habe. Falls Sie weitere Informationen benötigen oder Fragen haben, kommen Sie gerne auf mich zu. Die Bilder dürfen gerne etwas ausgeschnitten werden. Es geht in erster Linie darum, dass die Kunden erkennen, welche Art von Ofen sie zu Hause haben.

```html
<!DOCTYPE html>
<html lang="de">
<head>
<meta charset="utf-8">
<title>Ofenservice – Wartungsleistungen</title>
<link href="https://fonts.googleapis.com/css2?family=Open+Sans:wght@400;600;700&display=swap" rel="stylesheet">
<style>
  :root {
    --page-bg: #e6e4e1;
    --slate: #5f6a74;
    --slate-light: #6d7882;
    --panel-light: #f1f1f1;
    --paper: #ffffff;
    --ink: #2e2e2e;
    --ink-soft: #4a4a4a;
    --heading-grey: #8b9095;
    --accent: #c2652b;
  }
  * { box-sizing: border-box; margin: 0; padding: 0; }
  html, body { width: 1200px; height: 848px; overflow: hidden; }
  body {
    background: var(--page-bg);
    font-family: "Open Sans", Arial, sans-serif;
    color: var(--ink);
    position: relative;
  }
  .flyer {
    position: absolute; left: 104px; top: 70px;
    width: 992px; height: 710px;
    background: var(--paper);
    box-shadow: 0 3px 10px rgba(0,0,0,.25);
    overflow: hidden;
  }
  .panel { position: absolute; top: 0; height: 710px; }
  .panel--pellet { left: 0; width: 340px; }
  .panel--wood { left: 340px; width: 323px; background: var(--panel-light); }
  .panel--tile { left: 663px; width: 329px; background: var(--paper); }

  .pellet-info {
    position: absolute; left: 0; top: 0; width: 340px; height: 440px;
    background: linear-gradient(90deg, var(--slate) 0%, var(--slate-light) 100%);
    color: #fff; padding: 38px 20px 0 43px;
  }
  .panel-title { font-weight: 600; letter-spacing: .3px; }
  .pellet-info .panel-title { font-size: 30px; line-height: 40px; margin-bottom: 12px; }
  .intro { font-size: 12px; font-weight: 700; margin-bottom: 22px; }
  .service-list { list-style: none; font-size: 12px; line-height: 16px; }
  .service-list li { position: relative; padding-left: 13px; margin-bottom: 16px; }
  .service-list li::before { content: "•"; position: absolute; left: 0; top: 0; }
  .pellet-info .service-list li { margin-bottom: 16px; }

  .photo { position: absolute; }
  .photo--pellet {
    left: 0; top: 440px; width: 340px; height: 270px;
    background: linear-gradient(90deg, #dfe4ea 0%, #c9c4bc 35%, #e9e8e5 60%, #bcbcbc 100%);
  }
  .photo--wood-a { left: 0; top: 440px; width: 94px; height: 148px;
    background: linear-gradient(160deg, #5a4a3e, #2b2622 60%, #a5552a); }
  .photo--wood-b { left: 97px; top: 440px; width: 134px; height: 148px;
    background: linear-gradient(180deg, #6b3a22 0%, #c8631f 35%, #3a3a46 70%, #2a2d3a 100%); }
  .photo--wood-c { left: 235px; top: 440px; width: 88px; height: 148px;
    background: linear-gradient(180deg, #3c3a36 0%, #c9b85a 45%, #3a2320 100%); }
  .photo--tile {
    left: 0; top: 0; width: 329px; height: 200px;
    background: linear-gradient(120deg, #b57a3c 0%, #d9a564 40%, #eae6df 70%, #8a6a48 100%);
  }

  .wood-info { position: absolute; left: 28px; top: 42px; right: 16px; color: var(--ink-soft); }
  .wood-info .panel-title { color: var(--heading-grey); font-size: 29px; line-height: 27px; margin-bottom: 30px; }
  .wood-info .intro, .tile-info .intro { color: var(--ink-soft); margin-bottom: 24px; }
  .wood-info .service-list li, .tile-info .service-list li { margin-bottom: 16px; color: #555; }

  .tile-info { position: absolute; left: 30px; top: 222px; right: 16px; }
  .tile-info .panel-title { color: var(--accent); font-size: 31px; line-height: 32px; margin-bottom: 18px; }

  .price-box { position: absolute; border-left: 3px solid var(--accent); padding-left: 8px; }
  .price-box--pellet {
    left: 42px; top: 598px; width: 256px; height: 76px;
    background: rgba(255,255,255,.9); padding: 14px 0 0 14px; border-left: none;
  }
  .price-box--pellet::before {
    content: ""; position: absolute; left: 8px; top: 13px; width: 3px; height: 44px; background: var(--accent);
  }
  .price-box--wood { left: 34px; top: 610px; height: 58px; padding-top: 4px; }
  .price-box--tile { left: 30px; top: 540px; height: 126px; padding-top: 4px; }
  .price-label { font-size: 10px; font-weight: 700; color: var(--ink); line-height: 14px; }
  .price-main { font-size: 13px; color: var(--accent); line-height: 17px; }
  .price-alt { font-size: 11px; color: var(--ink); line-height: 17px; }
  .price-alt small { font-size: 9px; }
  .price-group + .price-group { margin-top: 14px; }
</style>
</head>
<body>
  <main class="flyer">
    <section class="panel panel--pellet">
      <div class="pellet-info">
        <h2 class="panel-title">Pelletöfen</h2>
        <p class="intro">Die Wartung beinhaltet:</p>
        <ul class="service-list">
          <li>Reinigung von Sichtscheibe, Brenntopf, Topfhalter, Zwischenboden, gesamter Feuerraum, sämtliche Rauchgaszüge und Aschebehälter</li>
          <li>Reinigung des Saugzuggebläses</li>
          <li>Überprüfung und Reinigung des Luftmen gensensors</li>
          <li>Überprüfung der elektrischen Zündung</li>
          <li>Überprüfung der Dichtungen (Türdichtung, Türglasdichtung, Putzdeckeldichtungen)</li>
          <li>Überprüfung der Temperaturwächter</li>
          <li>Probelauf des Gerätes</li>
        </ul>
      </div>
      <div class="photo photo--pellet" role="img" aria-label="Weißer Pelletofen mit Flamme neben einem Fenster mit Winterlandschaft"></div>
      <div class="price-box price-box--pellet">
        <p class="price-label">Preise:</p>
        <p class="price-main">Mit Wartungsvertrag: 140 € inkl. MwSt</p>
        <p class="price-alt">Ohne Wartungsvertrag: 180 € <small>inkl. MwST</small></p>
      </div>
    </section>

    <section class="panel panel--wood">
      <div class="wood-info">
        <h2 class="panel-title">Scheitholzöfen, Heizkassetten, Brennzellen, Holz- und Küchenherde</h2>
        <p class="intro">Die Wartung beinhaltet:</p>
        <ul class="service-list">
          <li>Reinigung Schamott Verkleidung, Sichtscheibe, Zwischenboden, gesamter Feuerraum, sämtliche Rauchgaszüge, Aschebehälter</li>
          <li>Reinigung der Abgasrohre<br>(bis 2 m gestreckte Länge)</li>
          <li>Überprüfung der Dichtungen (Türdichtung, Türglas-dichtung, Putzdeckeldichtungen)</li>
          <li>Probelauf des Gerätes</li>
        </ul>
      </div>
      <div class="photo photo--wood-a" role="img" aria-label="Schwarzer Kaminofen mit Feuer"></div>
      <div class="photo photo--wood-b" role="img" aria-label="Heizkassette und Brennzelle mit Feuer"></div>
      <div class="photo photo--wood-c" role="img" aria-label="Holzherd in einer Küche mit gefliester Wand"></div>
      <div class="price-box price-box--wood">
        <p class="price-label">Preise:</p>
        <p class="price-main">Mit Wartungsvertrag: 80 € inkl. MwSt</p>
        <p class="price-alt">Ohne Wartungsvertrag: 110 € <small>inkl. MwST</small></p>
      </div>
    </section>

    <section class="panel panel--tile">
      <div class="photo photo--tile" role="img" aria-label="Weißer Kachelofen mit Feuer in einem Holzhaus"></div>
      <div class="tile-info">
        <h2 class="panel-title">Grund-/<br>Kachelöfen</h2>
        <p class="intro">Die Wartung beinhaltet:</p>
        <ul class="service-list">
          <li>Reinigung Schamott Verkleidung, Sichtscheibe, Zwischenboden, gesamter Feuerraum, sämtliche Rauchgaszüge, Aschebehälter</li>
          <li>Reinigung der Abgasrohre<br>(bis 2 m gestreckte Länge)</li>
          <li>Überprüfung der Dichtungen (Türdichtung, Türglas-dichtung, Putzdeckeldichtungen)</li>
          <li>Probelauf des Gerätes</li>
        </ul>
      </div>
      <div class="price-box price-box--tile">
        <div class="price-group">
          <p class="price-label">Preise Kachelofen mit bis zu 4 Öffnungen</p>
          <p class="price-main">Mit Wartungsvertrag: 350 € inkl. MwSt</p>
          <p class="price-alt">Ohne Wartungsvertrag: 390 € <small>inkl. MwSt</small></p>
        </div>
        <div class="price-group">
          <p class="price-label">Preise Kachelofen mit nachgeschalteter Heizfläche</p>
          <p class="price-main">Mit Wartungsvertrag: 250 € inkl. MwSt</p>
          <p class="price-alt">Ohne Wartungsvertrag: 290 € <small>inkl. MwSt</small></p>
        </div>
      </div>
    </section>
  </main>
</body>
</html>
```